Landing Page für B2B-Softwareentwicklungsfirma
Zielgruppe
Wir sind eine (relativ kleine) B2B Softwareentwicklungsfirma, die Software zum Wetten auf Pferderennen erstellt.
Unsere Kunden sind Buchmacher und Rennbahnbetreiber.
Unsere Software läuft auf verschiedener Hardware (Touchscreen Terminals, Handy, Kassa, Webseite,...) und wird teilweise von Endkunden (Sportwetter) als auch Kunden-Mitarbeitern verwendet.
Was uns von anderen Softwarefirmen in diesem Bereich unterscheidet ist:
- Wir sind extrem verlässlich und unsere Software läuft störungsfrei
- Wir haben extrem viel Knowhow und ein großes Netzwerk im Bereich Pferdesport/-wetten
- Wir sind flexibel, gehen auf Kundenwünsche immer schnell und kosteneffizient ein
- Unsere softwaretechnischen Fähigkeiten sind ausgezeichnet (wir sind hauptsächlich Programmierer - weniger Businessleute).
- Wir sind für unsere Kunden immer persönlich, direkt und einfach ansprechbar (kleine Firma)
- Wir sind seit ca 15 Jahren erfolgreich im Markt, und auch Marktführer im deutschsprachigen Raum
- Wir haben ein sehr breites Produktportfolio (Terminal, Kassa, Mobile Webseite, Desktop Webseite, Backoffice, Risk Management)
- Wir legen viel Wert auf sauberes und auch modernes UI/UX-Design
Wir benötigen nun einen professionellen Webauftritt um in neue Märkte einzutreten.
Als ersten Schritt möchten wir gerne eine Single-Page Landingpage, die alle wichtigen Punkte im Überblick darstellt.
Aufgabenstellung
Das Design soll die Punkte aus der obigen Beschreibung über uns widerspiegeln, und auch unsere Werte:
Wichtig: Modern, Verlässlichkeit, Dynamisch, Kosteneffizient, Freundlich
Optional: Kreativ, Flexibilität
Wichtig ist auch der Bezug zum Pferderennsport!
Und dass wir eine B2B Softwarefirma sind!
Bitte beachten Sie unser neues Firmenlogo - siehe Anhang.
Die Landingpage soll eher hell, klar, offen, freundlich, sachlich sein.
Die Landingpage soll auf Mobile und Desktop funktionieren und gut aussehen.
Bitte verwenden Sie folgende Gliederung der Landingpage:
Sections:
....* Above the fold
........headline: horse betting software
........subheadline: Multi-product betting solution for bookmakers and racetrack operators.
................................Software production for land-based operations and online betting.
........call-to-action: get in touch
........secondary call-to-action: view products
........switch language
........links to other sections
....* Products
........Point of Sale
............Title: Quick and streamlined bet placement
............Short desc: Optimized bet placement solution for your bet shops and race tracks. Supports Windows-based touchscreen terminals and many different printers and scanners out of the box.
........Self-Service Terminals
............Title: Let users take control
............Short desc: Easy to use touchscreen software for new and professional punters. Running on any Windows-based hardware and adapted to your special needs.
........Web and Mobile Betting
............Title: Reach your target audience wherever they are
............Short desc: Allow your customers to enter their bets on any desktop or mobile browser.
........Bet Management
............Title: Stay in control of your meetings and bets
............Short desc: Browser-based Back-Office solution to control all your meetings,..

```html
<!DOCTYPE html>
<html lang="en">
<head>
<meta charset="utf-8">
<title>quellnet – Horse Betting Software</title>
<link href="https://fonts.googleapis.com/css2?family=Poppins:wght@400;500;600;700&display=swap" rel="stylesheet">
<style>
  :root{
    --navy:#0b5788;
    --ink:#1e2a3a;
    --text:#2b3340;
    --cyan:#36c7ea;
    --hero-bg:#f3f4f6;
    --page:#ffffff;
    --line:#eceef1;
    --card:#ffffff;
  }
  *{margin:0;padding:0;box-sizing:border-box}
  html,body{width:671px;height:1200px;overflow:hidden;background:var(--page)}
  body{position:relative;font-family:"Poppins",sans-serif;color:var(--text)}
  .abs{position:absolute}

  .hero{position:absolute;left:0;top:0;width:671px;height:383px;background:var(--hero-bg)}
  .brand{left:93px;top:15px;display:flex;align-items:center;gap:5px;font-size:15px;font-weight:600;color:var(--navy);letter-spacing:.5px}
  .brand i{width:7px;height:7px;background:var(--navy);display:block}
  .nav a{position:absolute;top:21px;font-size:7px;color:var(--ink);text-decoration:none}
  .nav .chev{display:inline-block;width:4px;height:4px;border-right:1px solid var(--ink);border-bottom:1px solid var(--ink);transform:rotate(45deg) translate(-1px,-1px);margin-left:4px}
  .btn{position:absolute;background:var(--navy);color:#fff;font-size:7px;font-weight:500;display:flex;align-items:center;justify-content:center;border-radius:3px;box-shadow:0 2px 4px rgba(11,87,136,.25)}
  .eyebrow{font-size:7px;font-weight:500;letter-spacing:1px;color:var(--cyan)}
  .hero h1{left:85px;top:111px;font-size:24.5px;line-height:28px;font-weight:700;color:var(--ink)}
  .hero p{left:85px;top:208px;width:205px;font-size:7.8px;line-height:13.5px}
  .link{left:190px;top:288px;font-size:7px;color:var(--navy);text-decoration:underline}

  .disc{left:340px;top:109px;width:182px;height:182px;border-radius:50%;background:var(--cyan)}
  .shot-race{left:432px;top:93px;width:119px;height:130px;border-radius:3px;background:linear-gradient(180deg,#2a1e1e 0,#3b3a36 45%,#f2f4f7 45%,#e9edf2 100%);box-shadow:0 2px 6px rgba(0,0,0,.2)}
  .horse{left:328px;top:150px;width:248px;height:146px;border-radius:16px;background:linear-gradient(160deg,rgba(70,70,70,.92),rgba(28,28,28,.92))}

  .center{left:0;width:671px;text-align:center}
  h2{font-size:20.5px;font-weight:700;color:var(--ink)}
  .lead{font-size:7.6px;line-height:12.6px}

  .mark{width:8px;height:8px;background:var(--cyan)}
  h3{font-size:14px;font-weight:600;color:var(--ink)}
  .desc{font-size:7.6px;line-height:12.6px;width:240px}
  .feat{position:absolute;width:72px;height:54px;background:var(--card);border-radius:3px;box-shadow:0 1px 4px rgba(0,0,0,.12);display:flex;flex-direction:column;align-items:center;justify-content:flex-end;padding-bottom:10px;font-size:7.4px;color:var(--ink)}
  .feat svg{position:absolute;top:10px;left:27px}
  .rule{height:1px;background:var(--line)}

  .shot{position:absolute;border-radius:3px;box-shadow:0 2px 6px rgba(0,0,0,.18)}
  .dash{position:absolute;width:4px;height:9px;background:var(--cyan);transform:skewY(-35deg)}
</style>
</head>
<body>

<header class="hero">
  <div class="abs brand"><i></i>quellnet</div>
  <nav class="nav">
    <a style="left:236px">Products<span class="chev"></span></a>
    <a style="left:282px">Why us?</a>
    <a style="left:328px">Company &amp; Team</a>
    <a style="left:405px">FAQ</a>
    <a style="left:492px">DE / EN</a>
  </nav>
  <div class="btn" style="left:535px;top:15px;width:44px;height:20px">Contact</div>

  <div class="abs eyebrow" style="left:85px;top:95px">HORSE BETTING SOFTWARE PROVIDERS</div>
  <h1 class="abs">The Reliable Way<br>To Manage<br>Your Horse Races</h1>
  <p class="abs">We provide multi-product betting solutions for bookmakers and racetrack operators.<br>Our proven software products are a perfect fit for land-based as well as online betting operations.</p>
  <div class="btn" style="left:85px;top:281px;width:89px;height:23px">View our products</div>
  <a class="abs link">Get in touch</a>

  <div class="abs disc"></div>
  <div class="abs shot-race" role="img" aria-label="Screenshot of live race view with odds and race card"></div>
  <div class="abs horse" role="img" aria-label="Photo of a galloping racehorse with jockey"></div>
</header>

<section>
  <div class="abs center eyebrow" style="top:429px">BETTING SOLUTIONS</div>
  <h2 class="abs center" style="top:446px">Our Products</h2>
  <p class="abs center lead" style="top:481px">Neque egestas congue quisque egestas diam in. Semper quis<br>lectus nulla at volutpat diam ut venenatis.</p>

  <div class="abs mark" style="left:90px;top:565px"></div>
  <h3 class="abs" style="left:90px;top:577px">Point of Sale</h3>
  <p class="abs desc" style="left:90px;top:608px">Lorem ipsum dolor sit amet, consectetur adipiscing elit, sed do eiusmod tempor incididunt ut labore et dolore magna aliqua.</p>
  <div class="feat" style="left:94px;top:648px">
    <svg width="18" height="18" viewBox="0 0 18 18"><circle cx="9" cy="9" r="8" fill="#4cbf7a"/><path d="M5 9.5l3 3 5-6" stroke="#fff" stroke-width="1.8" fill="none"/></svg>100% reliable</div>
  <div class="feat" style="left:174px;top:648px">
    <svg width="18" height="18" viewBox="0 0 18 18"><rect x="4" y="7" width="10" height="10" rx="3" fill="#f59a7a"/><rect x="7" y="1" width="3" height="8" rx="1.5" fill="#f59a7a"/></svg>Easy to use</div>
  <div class="feat" style="left:254px;top:648px">
    <svg width="18" height="18" viewBox="0 0 18 18"><path d="M2 14a7 7 0 0 1 14 0" stroke="#f27a3a" stroke-width="3" fill="none"/><path d="M9 14l5-6" stroke="#2f6fb5" stroke-width="2"/></svg>Performant</div>
  <div class="btn" style="left:90px;top:718px;width:89px;height:23px">More information</div>

  <div class="shot" style="left:389px;top:563px;width:159px;height:104px;background:linear-gradient(90deg,#e7ecf2 0 20%,#fafbfc 20%)" role="img" aria-label="Screenshot of back-office race card table"></div>
  <div class="shot" style="left:413px;top:653px;width:156px;height:88px;background:linear-gradient(180deg,#3e9a2a,#2f7f1f)" role="img" aria-label="Screenshot of fixed-odds race overview in green"></div>
  <div class="dash" style="left:559px;top:606px"></div><div class="dash" style="left:565px;top:620px"></div>
  <div class="dash" style="left:558px;top:628px"></div>

  <div class="abs rule" style="left:90px;top:777px;width:490px"></div>

  <div class="shot" style="left:103px;top:826px;width:159px;height:87px;background:linear-gradient(180deg,#101b2c,#1b2940)" role="img" aria-label="Screenshot of terminal race selection screen"></div>
  <div class="shot" style="left:117px;top:906px;width:186px;height:100px;background:linear-gradient(180deg,#3a4658 0 32%,#5f7fa6 32%,#3e5475)" role="img" aria-label="Screenshot of self-service terminal bet slip"></div>
  <div class="dash" style="left:103px;top:933px"></div><div class="dash" style="left:95px;top:940px"></div>
  <div class="dash" style="left:99px;top:953px"></div>

  <div class="abs mark" style="left:342px;top:827px"></div>
  <h3 class="abs" style="left:342px;top:839px">Self-Service Terminals</h3>
  <p class="abs desc" style="left:342px;top:870px">Lorem ipsum dolor sit amet, consectetur adipiscing elit, sed do eiusmod tempor incididunt ut labore et dolore magna aliqua.</p>
  <div class="feat" style="left:345px;top:910px;box-shadow:none;background:#fafbfc">
    <svg width="18" height="18" viewBox="0 0 18 18"><circle cx="9" cy="9" r="8" fill="#4cbf7a"/><path d="M5 9.5l3 3 5-6" stroke="#fff" stroke-width="1.8" fill="none"/></svg>100% reliable</div>
  <div class="feat" style="left:425px;top:910px;box-shadow:none;background:#fafbfc">
    <svg width="18" height="18" viewBox="0 0 18 18"><rect x="4" y="7" width="10" height="10" rx="3" fill="#f59a7a"/><rect x="7" y="1" width="3" height="8" rx="1.5" fill="#f59a7a"/></svg>Easy to use</div>
  <div class="feat" style="left:505px;top:910px;box-shadow:none;background:#fafbfc">
    <svg width="18" height="18" viewBox="0 0 18 18"><path d="M2 14a7 7 0 0 1 14 0" stroke="#f27a3a" stroke-width="3" fill="none"/><path d="M9 14l5-6" stroke="#2f6fb5" stroke-width="2"/></svg>Performant</div>
  <div class="btn" style="left:342px;top:984px;width:89px;height:23px">More information</div>

  <div class="abs rule" style="left:85px;top:1062px;width:491px"></div>
</section>

</body>
</html>
```